Webdesign für Projektmanagement
Zielgruppe
Projektmanagement und Projektsteuerung von Bauvorhaben für Projektentwickler und Bauträger.
Wesentliche Bereiche sind Wirtschaftliche Steuerung, Steuerung der Baustelle und Bauabläufe sowie Steuerung der Marketing und Vertriebsaktivitäten.
Aufgabenstellung
Orientierung am Logo. Logo und Visitenkarte liegen bei. Schriftart Prelo und Prelo Slab.

```html
<!DOCTYPE html>
<html lang="de">
<head>
<meta charset="utf-8">
<title>Vendahl Immobilien – Webdesign</title>
<link href="https://fonts.googleapis.com/css2?family=Bitter:ital,wght@0,400;0,600;0,700;1,400&family=Hind:wght@300;400;500;600&display=swap" rel="stylesheet">
<style>
:root{
  --navy:#03233f;
  --gold:#a08f4e;
  --gold-dark:#8f7f43;
  --paper:#f4f6f5;
  --white:#ffffff;
  --text:#4a5360;
  --muted:#a9b0b8;
  --stage:#f7f8f9;
  --slab:"Bitter", Georgia, serif;
  --sans:"Hind", Arial, sans-serif;
}
*{margin:0;padding:0;box-sizing:border-box}
html,body{width:1200px;height:3176px;overflow:hidden;background:var(--stage)}
.stage{width:966px;height:2557px;transform:scale(1.2422);transform-origin:0 0;position:relative}
.site{position:absolute;left:88px;top:78px;width:797px;height:2411px;background:var(--white);
  box-shadow:0 20px 60px rgba(3,35,63,.12);overflow:hidden;font-family:var(--sans);color:var(--text)}
.abs{position:absolute}

/* header + hero */
.navy-panel{left:393px;top:0;width:404px;height:399px;background:var(--navy)}
.light-area{left:0;top:399px;width:797px;height:412px;background:var(--paper)}
.light-under-hero{left:0;top:425px;width:393px;height:386px;background:var(--paper)}
.logo{left:38px;top:36px;font-family:var(--slab);font-weight:700;font-size:26px;color:var(--navy);letter-spacing:-.3px}
.nav{right:44px;top:46px;display:flex;gap:11px;font-size:13.5px;color:var(--white);font-weight:400}
.hero-photo{left:0;top:115px;width:583px;height:310px;
  background:linear-gradient(90deg,#8aa3bd 0%,#7d8fa8 20%,#4f6a8c 40%,#24395a 60%,#101c30 80%,#0c1526 100%)}
.hero-photo::after{content:"";position:absolute;inset:0;
  background:linear-gradient(180deg,rgba(255,255,255,0) 45%,rgba(40,35,30,.55) 100%)}
.hero-card{left:535px;top:232px;width:219px;height:216px;background:var(--white);padding:36px 28px;
  box-shadow:0 8px 24px rgba(0,0,0,.08)}
.hero-card h1{font-family:var(--slab);font-weight:700;font-size:18px;line-height:21px;color:var(--navy)}
.rule{width:20px;height:1.5px;background:var(--gold);margin:14px 0 16px}
.hero-card p{font-size:10.5px;line-height:18.5px;color:var(--text);font-weight:300}

/* beratung */
.consult-title{left:86px;top:518px;font-family:var(--slab);font-weight:600;font-size:19px;line-height:27px;color:var(--navy)}
.btn-gold{left:86px;top:586px;width:98px;height:24px;background:var(--gold);color:var(--white);
  font-size:8.5px;display:flex;align-items:center;justify-content:center;box-shadow:0 6px 12px rgba(160,143,78,.35)}
.consult-text{left:405px;top:520px;width:292px;font-size:10px;line-height:18.6px;font-weight:300;color:var(--text)}
.consult-text p+p{margin-top:10px}

/* gold band */
.gold-band{left:0;top:811px;width:797px;height:344px;background:var(--gold)}
.gold-band p{position:absolute;left:230px;top:86px;width:350px;font-family:var(--slab);font-weight:300;
  font-size:13.5px;line-height:22.3px;color:#f2ecd9}
.skyline{position:absolute;left:160px;top:232px;width:485px;height:112px;
  background:linear-gradient(180deg,rgba(110,110,90,.0) 0%,rgba(110,110,95,.55) 35%,#7b7660 100%)}

/* references */
.refs-title{left:86px;top:1226px;font-family:var(--slab);font-weight:600;font-size:19px;color:var(--navy)}
.tabs{left:86px;top:1270px;display:flex;gap:52px;font-size:13px;color:var(--muted);font-weight:400}
.tabs .active{color:var(--navy);border-bottom:1.5px solid var(--navy);padding-bottom:3px}
.ref-card{top:1358px;height:162px;background:var(--white);display:flex;box-shadow:0 6px 20px rgba(0,0,0,.07)}
.ref-img{width:141px;height:162px;flex:none}
.ref-body{padding:28px 20px 0 22px}
.ref-body h3{font-family:var(--slab);font-weight:700;font-size:7.5px;line-height:15px;color:#222}
.ref-body p{margin-top:14px;font-size:6.8px;line-height:12px;color:#555}

/* career */
.career{left:0;top:1601px;width:797px;height:359px;background:var(--navy)}
.career-photo{left:380px;top:1683px;width:417px;height:286px;
  background:linear-gradient(120deg,#e9f1f5 0%,#b7cfd9 40%,#7fa3b4 75%,#5f8595 100%)}
.career-title{left:86px;top:1680px;font-family:var(--slab);font-weight:700;font-size:19px;color:var(--white)}
.career-sub{left:86px;top:1710px;font-family:var(--slab);font-style:italic;font-size:14px;color:#e6e9ee}
.career-text{left:86px;top:1750px;width:215px;font-size:10px;line-height:18.6px;color:#e6e9ee;font-weight:300}
.btn-outline{left:86px;top:1853px;width:100px;height:23px;border:1px solid #e6e9ee;color:#e6e9ee;
  font-size:8.5px;display:flex;align-items:center;justify-content:center}

/* map + footer */
.map{left:0;top:1960px;width:797px;height:250px;background:linear-gradient(135deg,#efefef,#e6e6e6)}
.loc-title{left:86px;top:2253px;font-family:var(--slab);font-weight:600;font-size:19px;color:var(--navy)}
.address{left:503px;top:2262px;font-size:10px;line-height:17px;color:var(--navy)}
.address strong{font-weight:600}
</style>
</head>
<body>
<div class="stage">
  <div class="site">
    <div class="abs light-area"></div>
    <div class="abs light-under-hero"></div>
    <div class="abs navy-panel"></div>

    <header>
      <div class="abs logo">Vendahl</div>
      <nav class="abs nav"><span>Home</span><span>Leistungen</span><span>Referenzen</span><span>Über Uns</span><span>Kontakt</span></nav>
    </header>

    <div class="abs hero-photo" role="img" aria-label="Stadtansicht einer Hochhaus-Skyline vom Tag bis in die Nacht"></div>
    <div class="abs hero-card">
      <h1>Wir gestalten<br>Lebensraum</h1>
      <div class="rule"></div>
      <p>Profitieren Sie von unserer jahrzehntelangen Erfahrung im Immobilienmarkt</p>
    </div>

    <section>
      <h2 class="abs consult-title">Ganzheitliche<br>Beratung</h2>
      <div class="abs btn-gold">Jetzt beraten lassen</div>
      <div class="abs consult-text">
        <p>Die zunehmende Urbanisierung hat den Immobilienmarkt in den letzten Jahren nachhaltig verändert. Als Teil des größten Ballungszentrums Europas, hat dies starke Auswirkungen auf die Metropolregion Köln, Düsseldorf und Bonn. Begleitet wird diese Entwicklung durch vielschichtige städtebauliche Maßnahmen in der Region.</p>
        <p>Die Konsequenz aus dieser Entwicklung ist ein hoher Investitions-, Umnutzungs- und Projektentwicklungsbedarf bei Immobilien. Daraus entstanden ist ein für Investoren strukturell attraktiver Markt.</p>
      </div>
    </section>

    <section class="abs gold-band">
      <p>Wir sind ein interdisziplinär tätiges, mittelständisches Beratungs- und Dienstleistungsunternehmen. Wir bieten unseren Kunden maßgeschneiderte Dienstleis­tungen für ihr Immobilienportfolios an.</p>
      <div class="skyline" role="img" aria-label="Illustration einer flachen Stadtsilhouette mit Bäumen und Sonne"></div>
    </section>

    <section>
      <h2 class="abs refs-title">Unsere Referenzen</h2>
      <div class="abs tabs"><span class="active">Immobiliensanierung</span><span>Immobilienmanagement</span><span>Immobilienvertrieb und -marketing</span></div>

      <article class="abs ref-card" style="left:10px;width:363px">
        <div class="ref-img" role="img" aria-label="Foto eines weißen Einfamilienhauses mit Garage" style="background:linear-gradient(160deg,#9cc3e6,#e8e4dc 55%,#b9a98c)"></div>
        <div class="ref-body">
          <h3>Harbour Row One<br>24 Mill Lane, Eastbridge</h3>
          <p>Harbour Row is a compact residential quarter where shared courtyards and quiet streets meet city living. Built in two phases, it will offer 180 apartments, underground parking and planted common gardens.</p>
        </div>
      </article>
      <article class="abs ref-card" style="left:390px;width:364px">
        <div class="ref-img" role="img" aria-label="Foto eines modernen dunklen Apartmenthauses" style="background:linear-gradient(160deg,#8a9097,#3b3f44 55%,#6f6a60)"></div>
        <div class="ref-body">
          <h3>Quarry Court<br>24 Mill Lane, Eastbridge</h3>
          <p>Quarry Court is a compact residential quarter where shared courtyards and quiet streets meet city living. Built in two phases, it will offer 180 apartments, underground parking and planted common gardens.</p>
        </div>
      </article>
      <div class="abs ref-card" style="left:770px;width:27px;background:linear-gradient(180deg,#3d4f7a,#c48a4e)" role="img" aria-label="Foto einer Stadt am Abend"></div>
    </section>

    <section>
      <div class="abs career"></div>
      <div class="abs career-photo" role="img" aria-label="Foto eines Händedrucks zweier Geschäftsleute"></div>
      <h2 class="abs career-title">Karriere bei Vendahl</h2>
      <div class="abs career-sub">wir suchen Verstärkung</div>
      <p class="abs career-text">Wir sind ständig auf der Suche nach qualifizierten Mitarbeiterinnen und Mitarbeitern um unser Team von 60 Mitarbeitern weiter zu verstärken.</p>
      <div class="abs btn-outline">JETZT BEWERBEN</div>
    </section>

    <div class="abs map" role="img" aria-label="Straßenkarte der Region Düsseldorf mit Standortmarkierung"></div>

    <footer>
      <h2 class="abs loc-title">Unser Standort</h2>
      <address class="abs address" style="font-style:normal">
        <strong>Vendahl Immobilien GmbH</strong><br>
        Lindenhofstr. 14<br>
        40210 Düsseldorf<br>
        Tel: +49(0)211 - 5550120<br>
        Fax: +49(0)211 - 5550129<br>
        E-Mail: kontakt@vendahl-immobilien.de
      </address>
    </footer>
  </div>
</div>
</body>
</html>
```